Modern Business Card

Modern professional business card with more than just logo and demographic info. Something memorable.

We are a trendy/modern chiropractic group with an emphasis on neurology, hence the minimalist-type brain logo. We want to convey that modern and technical aspect with professionalism and the elite nature of our practice environment.

```html
<!DOCTYPE html>
<html lang="en">
<head>
<meta charset="utf-8">
<title>Vantage Spine &amp; Nerve – Business Card</title>
<link href="https://fonts.googleapis.com/css2?family=Alike&family=Khand:wght@600&display=swap" rel="stylesheet">
<style>
  :root {
    --backdrop: #b9b9b9;
    --brand-blue: #3e63a0;
    --brand-blue-deep: #395c96;
    --card-white: #f2f2f2;
    --ink: #3a3a3a;
    --on-blue: #f1f1f1;
    --on-blue-faint: rgba(255, 255, 255, 0.09);
  }
  * { margin: 0; padding: 0; box-sizing: border-box; }
  html, body {
    width: 1200px; height: 576px; overflow: hidden;
    background: var(--backdrop);
  }
  .canvas { position: relative; width: 1200px; height: 576px; }

  .card {
    position: absolute;
    border-radius: 10px;
    overflow: hidden;
  }
  .card-front {
    left: 82px; top: 139px; width: 484px; height: 293px;
    background: linear-gradient(180deg, var(--brand-blue) 0%, var(--brand-blue-deep) 100%);
    color: var(--on-blue);
    font-family: "Alike", Georgia, serif;
    text-align: center;
  }
  .front-backdrop-disc {
    position: absolute; left: 137px; top: 12px;
    width: 210px; height: 270px; border-radius: 105px;
    background: var(--on-blue-faint);
  }
  .front-wordmark { position: absolute; left: 0; right: 0; top: 98px; }
  .front-name {
    display: block; font-size: 66px; line-height: 1; letter-spacing: 1px;
  }
  .front-tagline {
    display: block; font-size: 34px; line-height: 1; margin-top: 4px; letter-spacing: 0.5px;
  }

  .card-back {
    left: 602px; top: 138px; width: 480px; height: 291px;
    background: var(--card-white);
    font-family: "Alike", Georgia, serif;
    color: var(--ink);
  }
  .back-brand {
    position: absolute; left: 40px; top: 62px; width: 196px;
    display: flex; flex-direction: column; align-items: center; gap: 18px;
    color: var(--brand-blue);
    font-size: 32px; line-height: 1; letter-spacing: 1px;
  }
  .brand-disc {
    width: 84px; height: 84px; border-radius: 50%;
    background: var(--brand-blue);
  }
  .contact-block { position: absolute; left: 261px; top: 64px; }
  .person-name {
    font-family: "Khand", "Arial Narrow", sans-serif; font-weight: 600;
    color: var(--brand-blue); font-size: 23px; line-height: 1;
  }
  .person-title { font-size: 13px; margin-top: 6px; }
  .contact-list { list-style: none; margin-top: 24px; }
  .contact-list li {
    display: flex; align-items: center; gap: 9px;
    font-size: 13px; height: 18px;
  }
  .contact-list svg { width: 11px; height: 11px; fill: var(--brand-blue); flex: none; }
  .address { font-size: 13px; line-height: 18px; margin-top: 8px; }
</style>
</head>
<body>
<main class="canvas">
  <section class="card card-front" aria-label="Card front">
    <div class="front-backdrop-disc" aria-hidden="true"></div>
    <div class="front-wordmark">
      <span class="front-name">VANTAGE</span>
      <span class="front-tagline">SPINE &amp; NERVE</span>
    </div>
  </section>

  <section class="card card-back" aria-label="Card back">
    <div class="back-brand">
      <span class="brand-disc" aria-hidden="true"></span>
      <span class="brand-name">VANTAGE</span>
    </div>
    <div class="contact-block">
      <div class="person-name">Alex Rowan Hale</div>
      <div class="person-title">Managing Director</div>
      <ul class="contact-list">
        <li>
          <svg viewBox="0 0 12 12" aria-hidden="true"><path d="M1 4c0-2 2-3 5-3s5 1 5 3l-2 1-1-2H4L3 5zM3 6h6l1 5H2z"/></svg>
          555-010-2040
        </li>
        <li>
          <svg viewBox="0 0 12 12" aria-hidden="true"><path d="M1 2h10v8H1z M1.5 2.5 6 6.5l4.5-4" fill="none" stroke="#3e63a0" stroke-width="1.2"/><path d="M1 2h10L6 6z"/></svg>
          alex@vantagespine.com
        </li>
        <li>
          <svg viewBox="0 0 12 12" aria-hidden="true"><circle cx="6" cy="6" r="5"/><path d="M1 6h10M6 1c-2.5 3-2.5 7 0 10M6 1c2.5 3 2.5 7 0 10" fill="none" stroke="#f2f2f2" stroke-width="0.8"/></svg>
          www.vantagespine.com
        </li>
      </ul>
      <p class="address">87 Harbor Lane, Millbrook,<br>Fairview, US 204518</p>
    </div>
  </section>
</main>
</body>
</html>
```